Business Card Design for Varomir Facility Services

We are looking for a Business Card Design for the Company "Varomir Facility Services."
Front side:
- Company Logo (small)
- Company Name, address, pohone, website and personal data.
- white background, for text e.g. company colors (blue or green like in the logo)
Please use following data:
Company data:
Varomir Facility Services Kostelac
Birkenhaldweg 14
6330 Cham
www.varomir-fs.ch
Person data:
Tarik Kostelac
Geschäftsführer
+41 76 519 47 83
info@varomir-fs.ch
Back side:
could be colored in blue or green
please use a big logo sing and some smaller icons to say what is all beeing offered in facility services, like cleaning, maintenance cleaning
industrial cleaning, caretaking, gardening, disposal. There is no need for everyone of the icons if there are similar or an icon is standing for more of them.
colors to use:
blue: HEX 246BB0
green: HEX 52B33E

```html
<!DOCTYPE html>
<html lang="de">
<head>
<meta charset="utf-8">
<title>Varomir Facility Services – Business Card</title>
<link rel="stylesheet" href="https://fonts.googleapis.com/css2?family=Poppins:wght@400;600&display=swap">
<style>
  :root {
    --brand-blue: #246bb0;
    --deep-blue: #0652b3;
    --brand-green: #52b33e;
    --text-grey: #555a60;
    --divider: #d2d4d8;
    --backdrop: #ecebe8;
    --card-white: #ffffff;
  }
  * { box-sizing: border-box; margin: 0; padding: 0; }
  html, body { width: 1125px; height: 1200px; overflow: hidden; }
  body {
    background: var(--backdrop);
    font-family: "Poppins", sans-serif;
    position: relative;
  }
  .card {
    position: absolute;
    left: 150px;
    width: 826px;
    height: 470px;
    box-shadow: 0 3px 10px rgba(0,0,0,0.25);
    overflow: hidden;
  }
  .card-front { top: 98px; background: var(--card-white); }
  .card-back { top: 632px; background: var(--deep-blue); }

  /* front */
  .front-brand {
    position: absolute;
    left: 40px; top: 150px;
    width: 340px;
    display: flex; align-items: center; gap: 16px;
  }
  .brand-dot {
    width: 46px; height: 46px; border-radius: 50%;
    background: var(--brand-blue);
    flex: none;
  }
  .brand-name {
    font-weight: 600;
    font-size: 38px;
    line-height: 1.1;
    color: var(--brand-blue);
  }
  .divider {
    position: absolute;
    left: 405px; top: 110px;
    width: 2px; height: 265px;
    background: linear-gradient(to bottom, transparent, var(--divider) 15%, var(--divider) 85%, transparent);
  }
  .details { position: absolute; left: 435px; top: 110px; }
  .person-name {
    font-weight: 600; font-size: 30px; line-height: 1.1;
    color: var(--deep-blue);
  }
  .person-role {
    font-size: 20px; color: var(--brand-green); line-height: 1.2;
  }
  .company-address {
    margin-top: 12px;
    font-size: 19.5px; line-height: 25px; color: var(--text-grey);
    font-style: normal;
  }
  .contact-list { list-style: none; margin-top: 10px; }
  .contact-list li {
    display: flex; align-items: center; gap: 10px;
    font-size: 19.5px; line-height: 27px; color: var(--text-grey);
  }
  .contact-list svg { width: 18px; height: 18px; flex: none; }
  .edge-stripe {
    position: absolute; left: 0; bottom: 0;
    width: 826px; height: 9px;
  }

  /* back */
  .back-brand {
    position: absolute;
    left: 0; right: 0; top: 140px;
    display: flex; justify-content: center; align-items: center; gap: 22px;
  }
  .back-brand .brand-dot { width: 64px; height: 64px; background: var(--card-white); }
  .back-brand .brand-name { color: var(--card-white); font-size: 50px; }
  .services {
    position: absolute; top: 312px; left: 0;
    width: 826px; height: 140px; list-style: none;
  }
  .service {
    position: absolute; top: 0;
    width: 130px; margin-left: -65px;
    text-align: center;
    font-size: 17px; line-height: 21px; color: var(--brand-green);
  }
  .service-badge {
    width: 78px; height: 78px; margin: 0 auto 8px;
    border: 2px solid var(--brand-green); border-radius: 50%;
    display: flex; align-items: center; justify-content: center;
  }
  .service-icon {
    width: 48px; height: 48px; border-radius: 50%;
    background: var(--brand-green); opacity: 0.85;
  }
</style>
</head>
<body>

<section class="card card-front" aria-label="Card front">
  <div class="front-brand">
    <span class="brand-dot"></span>
    <span class="brand-name">Varomir<br>Facility Services</span>
  </div>

  <div class="divider"></div>

  <div class="details">
    <h1 class="person-name">Tarik Kostelac</h1>
    <p class="person-role">Geschäftsführer</p>
    <address class="company-address">
      Varomir Facility Services Kostelac<br>
      Birkenhaldweg 14<br>
      6330 Cham
    </address>
    <ul class="contact-list">
      <li>
        <svg viewBox="0 0 18 18" aria-hidden="true"><rect x="4.5" y="1" width="9" height="16" rx="1.5" fill="none" stroke="#246bb0" stroke-width="1.6"/><line x1="7.5" y1="14.5" x2="10.5" y2="14.5" stroke="#246bb0" stroke-width="1.4"/></svg>
        +41 76 519 47 83
      </li>
      <li>
        <svg viewBox="0 0 18 18" aria-hidden="true"><rect x="1.5" y="4.5" width="15" height="10" fill="#246bb0"/><polyline points="1.5,4.5 9,10.5 16.5,4.5" fill="none" stroke="#fff" stroke-width="1.3"/></svg>
        info@varomir-fs.ch
      </li>
      <li>
        <svg viewBox="0 0 18 18" aria-hidden="true"><circle cx="9" cy="9" r="7.5" fill="#246bb0"/><path d="M5 6 Q8 5 8 8 Q6 10 7 13 M11 4 Q10 7 13 8 Q14 11 12 13" fill="none" stroke="#fff" stroke-width="1.2"/></svg>
        www.varomir-fs.ch
      </li>
    </ul>
  </div>

  <svg class="edge-stripe" viewBox="0 0 826 9" preserveAspectRatio="none" aria-hidden="true">
    <polygon points="0,0 538,0 533,9 0,9" fill="var(--brand-blue)"/>
    <polygon points="543,0 826,0 826,9 538,9" fill="var(--brand-green)"/>
  </svg>
</section>

<section class="card card-back" aria-label="Card back">
  <div class="back-brand">
    <span class="brand-dot"></span>
    <span class="brand-name">Varomir Facility Services</span>
  </div>

  <ul class="services">
    <li class="service" style="left:105px">
      <div class="service-badge"><span class="service-icon" role="img" aria-label="Broom icon"></span></div>
      Cleaning
    </li>
    <li class="service" style="left:224px">
      <div class="service-badge"><span class="service-icon" role="img" aria-label="Caretaker icon"></span></div>
      Caretaking
    </li>
    <li class="service" style="left:359px">
      <div class="service-badge"><span class="service-icon" role="img" aria-label="Gloves icon"></span></div>
      Maintenance<br>cleaning
    </li>
    <li class="service" style="left:486px">
      <div class="service-badge"><span class="service-icon" role="img" aria-label="Floor machine icon"></span></div>
      Industrial<br>cleaning
    </li>
    <li class="service" style="left:605px">
      <div class="service-badge"><span class="service-icon" role="img" aria-label="Watering can icon"></span></div>
      Gardening
    </li>
    <li class="service" style="left:719px">
      <div class="service-badge"><span class="service-icon" role="img" aria-label="Waste bin icon"></span></div>
      Disposal
    </li>
  </ul>
</section>

</body>
</html>
```